Electrician Letterhead Design MVR

We need some letterhead for our bills and other papers.
Customer address is on the right side (Swiss format)
A4 format

Design should also be applicable on Cards

Target Market(s)

Private Customers, Small Business

Industry/Entity Type

Electrician

Other font styles liked:
• incised 901

Colors
00AB8E
00BBA5
67D7C9
C6EFE9
E9F9F6

```html
<!DOCTYPE html>
<html lang="en">
<head>
<meta charset="utf-8">
<title>MVR Letterhead</title>
<link href="https://fonts.googleapis.com/css2?family=Lato:wght@400;700;900&family=Great+Vibes&display=swap" rel="stylesheet">
<style>
  :root {
    --brand: #00AB8E;
    --brand-deep: #009A84;
    --brand-light: #67D7C9;
    --backdrop: #E4E5E7;
    --paper: #FFFFFF;
    --ink: #2E2E2E;
    --ink-soft: #444444;
  }
  html, body {
    margin: 0;
    padding: 0;
    width: 1200px;
    height: 874px;
    overflow: hidden;
    background: var(--backdrop);
    font-family: 'Lato', sans-serif;
  }
  .letterhead {
    position: absolute;
    left: 303px;
    top: 17px;
    width: 594px;
    height: 840px;
    background: var(--paper);
    box-shadow: 0 4px 18px rgba(0,0,0,0.12);
    overflow: hidden;
    color: var(--ink);
  }
  .brand {
    position: absolute;
    left: 48px;
    top: 52px;
  }
  .brand-name {
    display: flex;
    align-items: center;
    gap: 8px;
    font-weight: 900;
    font-size: 46px;
    line-height: 1;
    color: var(--brand);
    letter-spacing: 1px;
  }
  .brand-mark {
    width: 14px;
    height: 14px;
    background: var(--brand);
  }
  .brand-tagline {
    margin-top: 4px;
    font-size: 9px;
    font-weight: 700;
    letter-spacing: 0.6px;
    color: var(--ink);
  }
  .header-rule {
    position: absolute;
    left: 48px;
    right: 40px;
    top: 122px;
    height: 1.5px;
    background: var(--brand);
  }
  .contact {
    position: absolute;
    right: 48px;
    top: 44px;
    font-size: 8.5px;
    line-height: 1.45;
    color: var(--ink);
  }
  .contact-row {
    display: flex;
    align-items: center;
    gap: 5px;
  }
  .contact-row svg { width: 8px; height: 8px; fill: var(--brand); }
  .contact-address { margin-bottom: 2px; }
  .letter {
    position: absolute;
    left: 62px;
    top: 150px;
    width: 460px;
    font-size: 10px;
    line-height: 1.45;
    color: var(--ink-soft);
  }
  .letter-date { font-size: 11px; margin-bottom: 14px; }
  .recipient { font-size: 11px; margin-bottom: 12px; }
  .recipient p { margin: 0; }
  .recipient .gap { margin-top: 10px; }
  .salutation {
    font-weight: 700;
    font-size: 13px;
    color: var(--ink);
    margin: 0 0 10px 40px;
  }
  .letter-body p { margin: 0 0 14px 40px; }
  .closing { margin: 20px 0 0 40px; font-size: 10px; }
  .signature {
    margin: 4px 0 0 70px;
    font-family: 'Great Vibes', cursive;
    font-size: 36px;
    color: var(--ink);
  }
  .footer-wave {
    position: absolute;
    left: 0;
    top: 0;
    width: 594px;
    height: 840px;
    pointer-events: none;
  }
</style>
</head>
<body>
  <main class="letterhead">
    <div class="brand">
      <div class="brand-name"><span>MVR</span><span class="brand-mark"></span></div>
      <div class="brand-tagline">Meister Volt Rhein GmbH</div>
    </div>

    <address class="contact" style="font-style: normal;">
      <div class="contact-address">42-07 Linden Rd 15,<br>Fairview, NY 11402</div>
      <div class="contact-row">
        <svg viewBox="0 0 10 10"><path d="M2 0.5 L4 2.5 L3 3.8 C3.8 5.3 4.7 6.2 6.2 7 L7.5 6 L9.5 8 L8 9.5 C4.5 9.2 0.8 5.5 0.5 2 Z"/></svg>
        <span>712-338-5024</span>
      </div>
      <div class="contact-row">
        <svg viewBox="0 0 10 10"><path d="M0.5 2 H9.5 V8 H0.5 Z M0.5 2 L5 5.5 L9.5 2" stroke="#fff" stroke-width="0.6"/></svg>
        <span>hello@mvrmail.com</span>
      </div>
      <div class="contact-row">
        <svg viewBox="0 0 10 10"><circle cx="5" cy="5" r="4.5"/><path d="M0.5 5 H9.5 M5 0.5 C3 3 3 7 5 9.5 M5 0.5 C7 3 7 7 5 9.5" stroke="#fff" stroke-width="0.5" fill="none"/></svg>
        <span>www.mvrelectric.com</span>
      </div>
    </address>

    <div class="header-rule"></div>

    <section class="letter">
      <div class="letter-date">Feb-03-2022</div>
      <div class="recipient">
        <p>Mr. Peter Lang</p>
        <p>President</p>
        <p class="gap">Brook Holdings</p>
        <p>456 Oak Lane, Suite# 8</p>
        <p>City, State, 340051</p>
      </div>
      <p class="salutation">Dear Mr. Peter</p>
      <div class="letter-body">
        <p>Lorem ipsum dolor sit amet, consectetur adipisicing elit, sed do eiusmod tempor incididunt ut labore et dolore magna aliqua. Ut enim ad minim veniam, quis nostrud exercitation ullamco laboris nisi ut aliquip ex ea commodo consequat. Duis aute irure dolor in reprehenderit in voluptate velit esse cillum dolore eu fugiat nulla pariatur.</p>
        <p>Lorem ipsum dolor sit amet, consectetur adipisicing elit, sed do eiusmod tempor incididunt ut labore et dolore magna aliqua. Ut enim ad minim veniam, quis nostrud exercitation ullamco laboris nisi ut aliquip ex ea commodo consequat. Duis aute irure dolor in reprehenderit in voluptate velit esse cillum dolore eu fugiat nulla pariatur.</p>
        <p>Lorem ipsum dolor sit amet, consectetur adipisicing elit, sed do eiusmod tempor incididunt ut labore et dolore magna aliqua. Ut enim ad minim veniam, quis nostrud exercitation ullamco laboris nisi ut aliquip ex ea commodo consequat.</p>
        <p>Excepteur sint occaecat cupidatat non proident, sunt in culpa qui officia deserunt mollit anim id est laborum. re et dolore magnam aliquam quaerat voluptatem.</p>
      </div>
      <div class="closing">Regards</div>
      <div class="signature">Daniel Brooks</div>
    </section>

    <svg class="footer-wave" viewBox="0 0 594 840" aria-hidden="true">
      <path d="M415 705 C505 655 560 575 570 478 L582 472 C578 575 520 655 415 705 Z" fill="var(--brand-light)"/>
      <path d="M285 840 C330 735 400 712 470 680 C540 648 580 585 594 488 L594 840 Z" fill="var(--brand-deep)"/>
    </svg>
  </main>
</body>
</html>
```